Modern Business Card

Modern professional business card with more than just logo and demographic info. Something memorable.

We are a trendy/modern chiropractic group with an emphasis on neurology, hence the minimalist-type brain logo. We want to convey that modern and technical aspect with professionalism and the elite nature of our practice environment.

```html
<!DOCTYPE html>
<html lang="en">
<head>
<meta charset="utf-8">
<title>Keystone Spine – Business Card</title>
<link rel="stylesheet" href="https://fonts.googleapis.com/css2?family=Cinzel:wght@500&family=Titillium+Web:wght@400;600&display=swap">
<style>
  :root {
    --stage: #1c1c1e;
    --card-white: #ffffff;
    --card-black: #0b0b0c;
    --pattern-tone: #161618;
    --brand-blue: #4a80c4;
    --band-grey: #5c5e5d;
    --band-black: #0a0a0a;
    --ink: #1a1a1a;
    --ink-soft: #555555;
    --ink-light: #ffffff;
  }
  * { box-sizing: border-box; margin: 0; padding: 0; }
  html, body { width: 1200px; height: 900px; overflow: hidden; }
  body {
    background: var(--stage);
    display: flex;
    flex-direction: column;
    align-items: center;
    justify-content: center;
    gap: 30px;
  }
  .card {
    position: relative;
    width: 700px;
    height: 400px;
    overflow: hidden;
  }

  /* Back side */
  .card-back { background: var(--card-black); }
  .card-back .pattern-field {
    position: absolute; inset: 0;
    background: radial-gradient(ellipse at center, var(--pattern-tone) 0%, var(--card-black) 85%);
  }
  .card-back .mark-dot {
    position: absolute;
    left: 50%; top: 150px;
    width: 46px; height: 46px;
    margin-left: -23px;
    border-radius: 50%;
    background: var(--brand-blue);
  }
  .card-back .wordmark {
    position: absolute;
    left: 0; right: 0; top: 282px;
    text-align: center;
    color: var(--ink-light);
    font-size: 26px;
  }

  /* Shared wordmark type */
  .wordmark {
    font-family: "Cinzel", serif;
    font-weight: 500;
    letter-spacing: 1px;
    line-height: 1;
  }

  /* Front side */
  .card-front { background: var(--card-white); }
  .card-front .wordmark {
    position: absolute;
    left: 62px; top: 52px;
    color: var(--ink);
    font-size: 36px;
  }
  .card-front .mark-dot {
    position: absolute;
    left: 580px; top: 112px;
    width: 64px; height: 64px;
    border-radius: 50%;
    background: var(--brand-blue);
  }
  .person { position: absolute; left: 62px; top: 168px; }
  .person-name {
    font-family: "Cinzel", serif;
    font-weight: 500;
    font-size: 27px;
    color: var(--ink-soft);
    letter-spacing: 0.5px;
    line-height: 1.1;
  }
  .person-role {
    font-family: "Titillium Web", sans-serif;
    font-size: 20px;
    color: var(--brand-blue);
    line-height: 1.1;
  }
  .divider {
    position: absolute;
    left: 62px; top: 250px;
    width: 265px; height: 2px;
    background: var(--ink);
  }
  .contact-list {
    position: absolute;
    left: 62px; top: 264px;
    list-style: none;
    font-family: "Titillium Web", sans-serif;
    font-size: 19px;
    color: var(--ink-soft);
  }
  .contact-list li {
    display: flex;
    align-items: center;
    gap: 10px;
    height: 28px;
  }
  .contact-list svg { width: 20px; height: 20px; flex: none; }
  .contact-list .domain { color: var(--brand-blue); font-weight: 600; }
  .bands { position: absolute; inset: 0; }
</style>
</head>
<body>

  <section class="card card-back" aria-label="Card back">
    <div class="pattern-field" role="img" aria-label="Faint repeating brand pattern across the dark background"></div>
    <div class="mark-dot"></div>
    <div class="wordmark">KEYSTONE SPINE</div>
  </section>

  <section class="card card-front" aria-label="Card front">
    <svg class="bands" viewBox="0 0 700 400" aria-hidden="true">
      <polygon points="320,400 700,155 700,262 488,400" fill="var(--brand-blue)"/>
      <polygon points="488,400 700,262 700,336 584,400" fill="var(--band-grey)"/>
      <polygon points="584,400 700,336 700,400" fill="var(--band-black)"/>
    </svg>

    <div class="wordmark">KEYSTONE SPINE</div>
    <div class="mark-dot"></div>

    <div class="person">
      <div class="person-name">MARCUS HALE</div>
      <div class="person-role">Training Specialist</div>
    </div>

    <div class="divider"></div>

    <ul class="contact-list">
      <li>
        <svg viewBox="0 0 20 20" aria-hidden="true"><circle cx="10" cy="10" r="8.5" fill="none" stroke="var(--brand-blue)" stroke-width="1.5"/><path d="M7 6.5c0 4 2.5 6.5 6.5 6.5l.8-1.6-2-1-1 1c-1.2-.5-2-1.3-2.5-2.5l1-1-1-2z" fill="var(--brand-blue)"/></svg>
        555.014.2290
      </li>
      <li>
        <svg viewBox="0 0 20 20" aria-hidden="true"><rect x="2" y="5" width="16" height="11" fill="none" stroke="var(--brand-blue)" stroke-width="1.5"/><path d="M2 5l8 6 8-6" fill="none" stroke="var(--brand-blue)" stroke-width="1.5"/></svg>
        m.hale@keystonespine.com
      </li>
      <li>
        <svg viewBox="0 0 20 20" aria-hidden="true"><circle cx="10" cy="10" r="8" fill="none" stroke="var(--brand-blue)" stroke-width="1.5"/><ellipse cx="10" cy="10" rx="3.5" ry="8" fill="none" stroke="var(--brand-blue)" stroke-width="1.3"/><path d="M2 10h16M3.5 6h13M3.5 14h13" stroke="var(--brand-blue)" stroke-width="1.2"/></svg>
        <span>www.<span class="domain">keystonespine</span>.com</span>
      </li>
    </ul>
  </section>

</body>
</html>
```